Up to the Challenge - PPT Template with Splash Slide

We are looking for a PPT template that has 4 slides.
1. Splash slide (Creative, fun, no content, a visual representation of the theme)
2. Section header slide
3. Content Slide
4. Content Slide, another design option
The theme is 'UP to the Challenge'. The design should reflect this theme.
The colors should be in Purple (#864B99), Blue (#0A80C2), and Green (#52B054).

```html
<!DOCTYPE html>
<html lang="en">
<head>
<meta charset="utf-8">
<title>Up to the Challenge – Slide Template</title>
<link rel="stylesheet" href="https://fonts.googleapis.com/css2?family=Playfair+Display:wght@500;600;700&family=Roboto:wght@400;500;700&display=swap">
<style>
  :root{
    --purple:#864B99;
    --blue:#0A80C2;
    --green:#52B054;
    --ink:#1f1f1f;
    --body:#3a3a3a;
    --page:#dcdcdc;
    --white:#ffffff;
  }
  *{margin:0;padding:0;box-sizing:border-box}
  html,body{width:1095px;height:1200px;overflow:hidden;background:var(--page)}
  body{position:relative;font-family:'Roboto',Arial,sans-serif;color:var(--body)}
  .slide{position:absolute;width:443px;height:249px;background:var(--white);overflow:hidden;box-shadow:0 6px 18px rgba(0,0,0,.12)}
  .col-left{left:76px}.col-right{left:576px}
  .row-1{top:63px}.row-2{top:338px}.row-3{top:613px}.row-4{top:888px}
  .serif{font-family:'Playfair Display',Georgia,serif}
  .abs{position:absolute}
  svg.layer{position:absolute;left:0;top:0;width:443px;height:249px}
  .brand-top{position:absolute;right:24px;top:6px;font-family:'Playfair Display',Georgia,serif;font-weight:600;font-size:17px;color:var(--white)}
  .brand-top.dark{color:var(--ink);top:12px}
  .footer-note{position:absolute;left:0;right:0;top:233px;text-align:center;font-size:4.6px;font-weight:500;color:#444}
  .heading{font-family:'Playfair Display',Georgia,serif;font-weight:600;font-size:17px;color:var(--ink)}
  .copy{font-size:6.7px;line-height:13.4px;text-align:justify;color:var(--body)}
  .social{position:absolute;left:0;right:0;display:flex;justify-content:center;align-items:center;gap:4px;font-size:7px;font-weight:500;color:var(--green)}
  .social .dot{width:9px;height:9px;border:1px solid var(--green);border-radius:50%}
  .photo-fill{position:absolute}
  .center-title{position:absolute;left:0;right:0;text-align:center;font-family:'Playfair Display',Georgia,serif;font-weight:700;color:var(--white);text-shadow:0 2px 6px rgba(0,0,0,.35)}
  .center-copy{position:absolute;left:40px;right:40px;text-align:center;font-size:8.4px;line-height:14.2px;color:var(--white)}
  .faq-item{position:absolute;width:170px;height:14px}
  .faq-badge{position:absolute;left:-7px;top:-7px;width:14px;height:14px;border-radius:50%;color:var(--white);font-size:6px;font-weight:700;display:flex;align-items:center;justify-content:center;box-shadow:0 1px 2px rgba(0,0,0,.25)}
  .faq-badge.q{background:var(--purple)}.faq-badge.a{background:var(--green)}
  .faq-text{position:absolute;left:15px;top:-6px;width:138px;font-size:5.3px;line-height:8px;font-weight:500;color:#444}
  .faq-text.answer{font-weight:700;color:#222}
</style>
</head>
<body>

<!-- Title slide -->
<section class="slide col-left row-1">
  <svg class="layer" viewBox="0 0 443 249">
    <defs>
      <linearGradient id="climbSky" x1="0" y1="0" x2="1" y2="1">
        <stop offset="0" stop-color="#6b5a3e"/><stop offset=".45" stop-color="#d9c9c8"/><stop offset="1" stop-color="#b7b7c6"/>
      </linearGradient>
    </defs>
    <path role="img" aria-label="Silhouette of a hiker climbing a hillside at sunrise" fill="url(#climbSky)" d="M0,0H443V150C400,168 350,176 300,168C220,152 130,118 0,147Z"/>
    <path fill="var(--purple)" d="M15,145C80,122 160,124 230,146C290,164 340,176 410,160C360,182 315,184 265,171C195,152 120,140 15,145Z"/>
  </svg>
  <div class="brand-top dark">Summit Rise</div>
  <div class="abs serif" style="left:0;right:0;top:170px;text-align:center;font-size:13px;font-weight:600;color:var(--ink)">Welcome To</div>
  <div class="abs serif" style="left:0;right:0;top:186px;text-align:center;font-size:24px;font-weight:600;color:var(--ink)">Summit Rise</div>
  <div class="social" style="top:227px"><span class="dot"></span>Summit Rise</div>
</section>

<!-- Why choose us -->
<section class="slide col-right row-1">
  <svg class="layer" viewBox="0 0 443 249">
    <path fill="var(--purple)" d="M0,0H443V35C420,48 380,52 340,50C250,45 180,5 110,12C60,16 20,28 0,36Z"/>
    <path fill="none" stroke="var(--blue)" stroke-width="2.5" d="M92,13C175,10 245,46 345,50"/>
    <defs><linearGradient id="rockSky" x1="0" y1="0" x2="1" y2="0"><stop offset="0" stop-color="#e6e8ea"/><stop offset="1" stop-color="#6e5c4d"/></linearGradient></defs>
    <circle role="img" aria-label="Woman climbing a rock face" cx="112" cy="137" r="84" fill="url(#rockSky)" stroke="var(--green)" stroke-width="3"/>
    <rect x="0" y="236" width="98" height="2.5" fill="var(--green)"/>
    <rect x="345" y="236" width="98" height="2.5" fill="var(--green)"/>
  </svg>
  <div class="brand-top">Summit Rise</div>
  <div class="abs heading" style="left:221px;top:60px">Why Choose Us?</div>
  <p class="abs copy" style="left:221px;top:84px;width:199px">Lorem ipsum dolor sit amet, consectetur adipiscing elit, sed do eiusmod tempor incididunt ut labore et dolore magna aliqua. Ut enim ad minim veniam, quis nostrud exercitation ullamco laboris nisi ut aliquip ex ea commodo consequat. Duis aute irure dolor in reprehenderit in voluptate velit esse cillum dolore eu fugiat nulla pariatur. Excepteur sint occaecat cupidatat non proident, sunt in culpa qui officia deserunt mollit anim id est laborum perspiciatis unde omnis iste natus voluptatem accusantium doloremque laudantium, totam rem aperiam, eaque ipsa quaed.</p>
  <div class="footer-note">© 2024 Summit Rise. All Rights Reserved</div>
</section>

<!-- About us -->
<section class="slide col-left row-2">
  <svg class="layer" viewBox="0 0 443 249">
    <path fill="var(--purple)" d="M0,0H443V35C420,48 380,52 340,50C250,45 180,5 110,12C60,16 20,28 0,36Z"/>
    <path fill="none" stroke="var(--blue)" stroke-width="2.5" d="M92,13C175,10 245,46 345,50"/>
    <rect x="0" y="236" width="98" height="2.5" fill="var(--green)"/>
    <rect x="345" y="236" width="98" height="2.5" fill="var(--green)"/>
  </svg>
  <div class="brand-top">Summit Rise</div>
  <div class="abs heading" style="left:23px;top:67px">About Us</div>
  <p class="abs copy" style="left:23px;top:91px;width:198px">Lorem ipsum dolor sit amet, consectetur adipiscing elit, sed do eiusmod tempor incididunt ut labore et dolore magna aliqua. Ut enim ad minim veniam, quis nostrud exercitation ullamco laboris nisi ut aliquip ex ea commodo consequat. Duis aute irure dolor in reprehenderit in voluptate velit esse cillum dolore eu fugiat nulla pariatur. Excepteur sint occaecat cupidatat non proident, sunt in culpa qui officia deserunt mollit anim id est laborum perspiciatis unde omnis iste natus voluptatem accusantium doloremque laudantium, totam rem aperiam, eaque ipsa quaed.</p>
  <div class="photo-fill" role="img" aria-label="Hand reaching for a red ladder against a blue sky" style="left:248px;top:67px;width:172px;height:148px;border-radius:6px;background:linear-gradient(135deg,#2f7fb0,#1d6b99 55%,#b8322a 100%)"></div>
  <div class="footer-note">© 2024 Summit Rise. All Rights Reserved</div>
</section>

<!-- Green section header -->
<section class="slide col-right row-2" role="img" aria-label="Faint dart in a target on green" style="background:radial-gradient(ellipse at 60% 80%,#4aa64c,#52B054 70%)">
  <div class="abs" style="left:39px;top:55px;width:366px;height:138px;border:1px solid rgba(255,255,255,.85)"></div>
  <div class="center-title" style="top:70px;font-size:38px">Lorem ipsum dolor</div>
  <p class="center-copy" style="top:128px">Lorem ipsum dolor sit amet, consectetur adipiscing elit, sed do eiusmod tempor incididunt ut labore et dolore magna aliquat enim ad minim veniam, quis nostrud exercitation ullamco laboris nisi ut aliquip ex ea commodo consequa Duis aute irured.</p>
</section>

<!-- Splash slide -->
<section class="slide col-left row-3" role="img" aria-label="Silhouette of a person with raised arms on a mountain peak at sunset" style="background:linear-gradient(180deg,#6d7a8c 0%,#c98a62 40%,#e3a062 52%,#6b3f2a 72%,#2a1a16 100%)">
  <div class="center-title" style="top:100px;font-size:36px">Summit Rise</div>
</section>

<!-- FAQ -->
<section class="slide col-right row-3">
  <svg class="layer" viewBox="0 0 443 249">
    <path fill="var(--purple)" d="M0,0H443V35C420,48 380,52 340,50C250,45 180,5 110,12C60,16 20,28 0,36Z"/>
    <path fill="none" stroke="var(--blue)" stroke-width="2.5" d="M92,13C175,10 245,46 345,50"/>
    <rect x="0" y="236" width="98" height="2.5" fill="var(--green)"/>
    <rect x="345" y="236" width="98" height="2.5" fill="var(--green)"/>
  </svg>
  <div class="brand-top">Summit Rise</div>
  <div class="abs heading" style="left:40px;top:33px">Faq</div>

  <div class="faq-item" style="left:48px;top:73px"><span class="faq-badge q">Q</span><p class="faq-text">Lorem ipsum dolor sit amet, consectetur adipiscing elit, sed do eiusmod tempor incididunt</p></div>
  <div class="faq-item" style="left:48px;top:96px"><span class="faq-badge a">A</span><p class="faq-text answer">Lorem ipsum dolor sit amet, consectetur adipiscing elit, sed do eiusmod tempor incididunt</p></div>
  <div class="faq-item" style="left:48px;top:132px"><span class="faq-badge q">Q</span><p class="faq-text">Lorem ipsum dolor sit amet, consectetur adipiscing elit, sed do eiusmod tempor incididunt</p></div>
  <div class="faq-item" style="left:48px;top:155px"><span class="faq-badge a">A</span><p class="faq-text answer">Lorem ipsum dolor sit amet, consectetur adipiscing elit, sed do eiusmod tempor incididunt</p></div>
  <div class="faq-item" style="left:48px;top:190px"><span class="faq-badge q">Q</span><p class="faq-text">Lorem ipsum dolor sit amet, consectetur adipiscing elit, sed do eiusmod tempor incididunt</p></div>
  <div class="faq-item" style="left:48px;top:214px"><span class="faq-badge a">A</span><p class="faq-text answer">Lorem ipsum dolor sit amet, consectetur adipiscing elit, sed do eiusmod tempor incididunt</p></div>

  <div class="faq-item" style="left:243px;top:73px"><span class="faq-badge q">Q</span><p class="faq-text">Lorem ipsum dolor sit amet, consectetur adipiscing elit, sed do eiusmod tempor incididunt</p></div>
  <div class="faq-item" style="left:243px;top:96px"><span class="faq-badge a">A</span><p class="faq-text answer">Lorem ipsum dolor sit amet, consectetur adipiscing elit, sed do eiusmod tempor incididunt</p></div>
  <div class="faq-item" style="left:243px;top:132px"><span class="faq-badge q">Q</span><p class="faq-text">Lorem ipsum dolor sit amet, consectetur adipiscing elit, sed do eiusmod tempor incididunt</p></div>
  <div class="faq-item" style="left:243px;top:155px"><span class="faq-badge a">A</span><p class="faq-text answer">Lorem ipsum dolor sit amet, consectetur adipiscing elit, sed do eiusmod tempor incididunt</p></div>
  <div class="faq-item" style="left:243px;top:190px"><span class="faq-badge q">Q</span><p class="faq-text">Lorem ipsum dolor sit amet, consectetur adipiscing elit, sed do eiusmod tempor incididunt</p></div>
  <div class="faq-item" style="left:243px;top:214px"><span class="faq-badge a">A</span><p class="faq-text answer">Lorem ipsum dolor sit amet, consectetur adipiscing elit, sed do eiusmod tempor incididunt</p></div>

  <div class="footer-note">© 2024 Summit Rise. All Rights Reserved</div>
</section>

<!-- Blue section header -->
<section class="slide col-left row-4" role="img" aria-label="Faint silhouette of a climber holding a trophy on blue" style="background:linear-gradient(180deg,#2b88c0,#1f79b3 60%,#136aa6)">
  <div class="center-title" style="top:70px;font-size:36px">Perspiciatis Unde</div>
  <p class="center-copy" style="top:125px;left:45px;right:45px">Lorem ipsum dolor sit amet, consectetur adipiscing elit, sed do eiusmod tempor incididunt ut labore et dolore magna aliquat enim ad minim veniam, quis nostrud exercitation ullamco laboris nisi ut aliquip ex ea commodo consequa Duis aute irured.</p>
</section>

<!-- Thank you -->
<section class="slide col-right row-4">
  <svg class="layer" viewBox="0 0 443 249">
    <defs>
      <linearGradient id="peakSky" x1="0" y1="0" x2="0" y2="1">
        <stop offset="0" stop-color="#9fb4c6"/><stop offset=".45" stop-color="#e6dccb"/><stop offset=".75" stop-color="#8a7a66"/><stop offset="1" stop-color="#5d5a55"/>
      </linearGradient>
    </defs>
    <path role="img" aria-label="Hiker with raised arms on a mountain summit above the clouds" fill="url(#peakSky)" d="M0,0H443V150C400,168 350,176 300,168C220,152 130,118 0,147Z"/>
    <path fill="var(--purple)" d="M15,145C80,122 160,124 230,146C290,164 340,176 410,160C360,182 315,184 265,171C195,152 120,140 15,145Z"/>
  </svg>
  <div class="brand-top dark">Summit Rise</div>
  <div class="abs serif" style="left:0;right:0;top:173px;text-align:center;font-size:25px;font-weight:600;color:var(--ink)">Thank you</div>
  <div class="social" style="top:215px"><span class="dot"></span>Summit Rise</div>
</section>

</body>
</html>
```